Website for IT consulting Company

I need a website upgrade, the existing site content is ok, I would also like to add a testimonial page, the site should be something that is easy for us to update content. You use the content from www.kelvanbrook.com as an example. I will also post update logo and artwork. I also need a contact form with some type of validation or captcha.

I added Coded to the Project

Please omit Address maps

Target Market(s)

small business, service oriented companies. We provide IT Consulting, support and mangement

Industry/Entity Type

Information Technology

Coding

Number of Pages Required

1 page

Font styles to use
Serif
Sans Serif

Requirements
Must have
• Contain logo attached, and content from existing web site www.kelvanbrook.com.
• Also need to update content easily, and be movable to different platforms.
• There is a catch phrase
• "Let us worry about your technology…” “ so you don’t have to!”
• Should be included.
Nice to have
• Testimonial page, Project page where we can post new and past projects and pictures
Should not have
• none

```html
<!DOCTYPE html>
<html lang="en">
<head>
<meta charset="utf-8">
<title>Kelvanbrook Technology Group</title>
<link href="https://fonts.googleapis.com/css2?family=Maven+Pro:wght@400;500;600;700&family=Roboto:wght@400;500&display=swap" rel="stylesheet">
<style>
:root{
  --blue:#1a84cf;
  --blue-dark:#17599b;
  --blue-bar:#1b8fd8;
  --ink:#1c1c1c;
  --text:#5a5a5a;
  --link:#2680c4;
  --band:#e8f0fa;
  --white:#ffffff;
}
*{margin:0;padding:0;box-sizing:border-box}
html,body{width:1200px;height:2679px;overflow:hidden;background:var(--white)}
body{position:relative;font-family:"Roboto",Arial,sans-serif;color:var(--text)}
.abs{position:absolute}
h1,h2,h3,h4{font-family:"Maven Pro",Arial,sans-serif;font-weight:500;color:var(--ink)}

/* hero */
.hero{left:0;top:0;width:1200px;height:640px;background:linear-gradient(100deg,#f1f3f6 0%,#dfe4ea 40%,#c9d1da 70%,#e3e7ec 100%)}
.hero-photo{left:80px;top:170px;width:520px;height:470px;background:radial-gradient(ellipse at 50% 45%,#6b4a3c 0%,#3a2a28 35%,rgba(200,205,212,0) 70%)}
.hero-cut{left:0;top:520px}
.brand{left:0;top:40px;width:1200px;text-align:center;font-family:"Maven Pro",sans-serif;font-weight:700;font-size:44px;color:var(--blue);letter-spacing:1px}
.brand .mark{display:inline-block;width:32px;height:32px;background:var(--blue);margin-right:14px;vertical-align:-3px}
.tagline{left:0;top:94px;width:1200px;text-align:center;font-size:12px;color:var(--blue);font-style:italic}
.nav-line{left:0;top:113px;width:1200px;height:1px;background:#9aa6b3}
.nav{left:0;top:113px;width:1200px;height:51px}
.nav a{position:absolute;top:0;height:51px;line-height:51px;font-size:17px;color:#222;text-decoration:none;transform:translateX(-50%)}
.nav a.active{left:156px;width:105px;text-align:center;background:var(--blue);color:var(--white)}
.arrow-box{top:286px;width:77px;height:53px;background:var(--white);border:1px solid #6a8fb7;font-size:34px;line-height:48px;text-align:center;color:#123;font-weight:700}
.hero-title{right:111px;top:312px;text-align:right;font-family:"Maven Pro",sans-serif;font-weight:700;font-size:46px;line-height:54px;color:#111;letter-spacing:-1px}
.hero-sub{right:111px;top:420px;font-size:23px;color:#111}

/* headings with square */
.sec-title{display:flex;align-items:center;justify-content:center;gap:8px;font-size:40px}
.sq{display:inline-block;width:30px;height:30px;background:var(--blue);flex:none}
.sq.sm{width:24px;height:24px}
.read-more{font-size:17px;color:#111;text-decoration:underline}
.read-more b{text-decoration:none;font-size:22px;margin-left:4px}

/* about */
.about-title{left:0;top:682px;width:1200px}
.about-text{left:162px;top:750px;width:876px;text-align:center;font-size:14.5px;line-height:25px}
.about-more{left:0;top:830px;width:1200px;text-align:center}
.service{top:904px;width:330px}
.service .head{display:flex;align-items:center;gap:14px;height:60px}
.service .icon{width:52px;height:52px;flex:none}
.service h3{font-size:19px;line-height:25px;color:#111}
.service h3.blue{color:var(--link)}
.service p{margin-top:10px;font-size:14.5px;line-height:23px}
.service .read-more{display:inline-block;margin-top:4px;font-size:16px}
.service .read-more.blue{color:var(--link);text-decoration:none}

/* band */
.band{left:0;top:1121px;width:1200px;height:808px;background:linear-gradient(180deg,#edf3fb 0%,#e3ecf8 60%,#eef3fb 100%)}
.img-block{background:linear-gradient(135deg,#0d2548,#1a4d8c 55%,#0b1c38)}
.img-cyber{left:77px;top:1157px;width:523px;height:333px}
.img-team{left:600px;top:1552px;width:522px;height:334px;background:linear-gradient(135deg,#e9edf1,#c7cfd8 45%,#2a6fc2 80%,#dfe4ea)}
.support-title{right:79px;top:1150px;font-size:29px;justify-content:flex-end}
.support-text{right:79px;top:1200px;width:500px;text-align:right;font-size:14.5px;line-height:25px}
.feature{font-size:15.5px;color:#222;display:flex;align-items:center;gap:10px}
.feature svg{width:22px;height:22px}
.out-title{left:79px;top:1549px;font-size:29px;justify-content:flex-start}
.out-text{left:79px;top:1600px;width:430px;font-size:14.5px;line-height:25px}
.out-more{left:79px;top:1728px}

/* testimonial */
.testi-title{left:0;top:1975px;width:1200px}
.testi-sub{left:0;top:2048px;width:1200px;text-align:center;font-size:14.5px}
.quote-mark{left:220px;top:2060px;font-family:"Maven Pro",sans-serif;font-size:90px;line-height:90px;color:#4fa0dd}
.quote-box{left:209px;top:2090px;width:780px;height:124px;background:var(--blue);border-radius:12px;padding:20px 34px;color:#eaf4fc;font-size:14.5px;line-height:25px}
.quote-tail{left:262px;top:2212px}
.client{left:302px;top:2222px;font-size:16px;color:#111}
.dots{left:538px;top:2264px;display:flex;gap:3px}
.dots span{width:15px;height:15px;border:1.5px solid var(--blue)}
.dots span.on{background:var(--blue)}

/* footer */
.footer{left:0;top:2332px;width:1200px;height:293px;background:var(--blue-dark)}
.f-col{top:2382px;color:#e4eef8}
.f-col h4{color:#fff;font-size:18px;letter-spacing:.5px;margin-bottom:22px}
.f-links li{list-style:none;font-size:14px;line-height:25px}
.f-news p{font-size:14.5px;line-height:24px;color:#aac4e0;width:270px}
.f-input{margin-top:14px;width:260px;height:32px;border-bottom:1px solid #b7cbe2;font-size:13px;color:#9fb9d6;padding:8px 0 0 14px;position:relative}
.f-input svg{position:absolute;right:10px;top:6px}
.f-btn{margin:10px 0 0 50px;width:162px;height:42px;background:#fff;color:var(--blue-dark);border-radius:3px;text-align:center;line-height:42px;font-family:"Maven Pro",sans-serif;font-size:17px}
.f-contact .row{display:flex;gap:16px;font-size:14px;line-height:25px;margin-bottom:16px}
.f-contact svg{flex:none;margin-top:5px}
.copy{left:0;top:2625px;width:1200px;height:54px;background:var(--blue-bar);text-align:center;line-height:54px;color:#123a66;font-size:15px}
.copy b{color:#0f2d55;font-weight:500}
</style>
</head>
<body>

<!-- hero -->
<div class="abs hero"></div>
<div class="abs hero-photo" role="img" aria-label="Photo of a professional woman working on a laptop in an office"></div>
<svg class="abs hero-cut" width="1200" height="122" viewBox="0 0 1200 122"><polygon points="0,115 600,70 1200,0 1200,122 0,122" fill="#ffffff"/></svg>
<div class="abs brand"><span class="mark"></span>KELVANBROOK</div>
<div class="abs tagline">Let us worry about your technology… so you don't have to!</div>
<div class="abs nav-line"></div>
<nav class="abs nav">
  <a class="active" href="#">Home</a>
  <a style="left:289px" href="#">About</a>
  <a style="left:430px" href="#">Services</a>
  <a style="left:571px" href="#">Clients</a>
  <a style="left:704px" href="#">Careers</a>
  <a style="left:857px" href="#">Testimonial</a>
  <a style="left:1021px" href="#">Contact us</a>
</nav>
<div class="abs arrow-box" style="left:0">«</div>
<div class="abs arrow-box" style="left:1123px">»</div>
<h1 class="abs hero-title">IT SOLUTIONS THAT WORK<br>FOR YOUR BUSINESS.</h1>
<div class="abs hero-sub">A full service technology company</div>

<!-- about -->
<h2 class="abs sec-title about-title"><span class="sq"></span>ABOUT US</h2>
<p class="abs about-text">Kelvanbrook Technology Group, Inc. was established in 1991. Our mission is helping businesses and individuals realize a Return on Investment by implementing today's advanced technologies. As a small business we understand the importance of technology and personalized attention.Every member of our support team has worked with both large and small companies...</p>
<div class="abs about-more"><span class="read-more">READ MORE<b>»</b></span></div>

<div class="abs service" style="left:79px">
  <div class="head">
    <svg class="icon" viewBox="0 0 52 52"><circle cx="30" cy="16" r="9" fill="none" stroke="#1a84cf" stroke-width="4" stroke-dasharray="4 3"/><circle cx="30" cy="16" r="3" fill="#1a84cf"/><path d="M4 40 h14 l10 -6 h12 v4 l-18 10 h-18z" fill="#1a84cf"/></svg>
    <h3>Managed IT Solutions</h3>
  </div>
  <p>Our staff will design, service, administer and maintain your IT needs. We are well versed on all major operating system...</p>
  <span class="read-more">READ MORE<b>»</b></span>
</div>
<div class="abs service" style="left:443px">
  <div class="head">
    <svg class="icon" viewBox="0 0 52 52"><rect x="4" y="14" width="44" height="28" fill="none" stroke="#333" stroke-width="3"/><circle cx="26" cy="28" r="7" fill="#1a84cf"/><path d="M10 4 v10 M42 4 v10 M4 48 h44" stroke="#333" stroke-width="3"/></svg>
    <h3 class="blue">Remote Diagnostic and Support</h3>
  </div>
  <p>Do you need a quick solution to a technical problem? With our live remote-assistance tool, a member of our support team...</p>
  <span class="read-more blue">READ MORE<b>»</b></span>
</div>
<div class="abs service" style="left:807px">
  <div class="head">
    <svg class="icon" viewBox="0 0 52 52"><rect x="4" y="4" width="24" height="36" fill="none" stroke="#333" stroke-width="3"/><rect x="20" y="22" width="28" height="26" fill="#fff" stroke="#333" stroke-width="3"/><path d="M28 35 l4 -4 M28 35 l4 4 M40 35 l-4 -4 M40 35 l-4 4" stroke="#1a84cf" stroke-width="2.5"/><path d="M9 12 h14 M9 20 h10" stroke="#1a84cf" stroke-width="3"/></svg>
    <h3 class="blue">IT Infrastructure Design and Installation</h3>
  </div>
  <p>Do you have more than one site? Do you need remote access? We can design and implement LANS/WANS and VPN's...</p>
  <span class="read-more blue">READ MORE<b>»</b></span>
</div>

<!-- band -->
<div class="abs band"></div>
<div class="abs img-block img-cyber" role="img" aria-label="Photo of a man typing at a keyboard surrounded by digital security labels"></div>
<h2 class="abs sec-title support-title"><span class="sq sm"></span>IT SUPPORT SOLUTIONS</h2>
<p class="abs support-text">Kelvanbrook is a technology solution provider based in Fairhaven, Texas.Kelvanbrook has the experience, the tools, high-level technology solutions and training to power your business and your work force.</p>
<div class="abs feature" style="left:664px;top:1292px"><svg viewBox="0 0 22 22"><path d="M5 16 a5 5 0 0 1 1-9 a6 6 0 0 1 11 2 a4 4 0 0 1 0 7z" fill="#1a84cf"/></svg>Network Asministration</div>
<div class="abs feature" style="left:923px;top:1292px"><svg viewBox="0 0 22 22"><circle cx="11" cy="12" r="2.5" fill="#1a84cf"/><path d="M6 7 a7 7 0 0 0 0 10 M16 7 a7 7 0 0 1 0 10" stroke="#1a84cf" stroke-width="2" fill="none"/></svg>Wireless Network</div>
<div class="abs feature" style="left:664px;top:1336px"><svg viewBox="0 0 22 22"><path d="M11 2 l8 3 v6 c0 5 -4 8 -8 9 c-4 -1 -8 -4 -8 -9 v-6z" fill="#1a84cf"/></svg>Antivirus Solution</div>
<div class="abs feature" style="left:923px;top:1336px"><svg viewBox="0 0 22 22"><path d="M4 18 c4 -8 10 -10 14 -14" stroke="#1a84cf" stroke-width="2.5" fill="none"/><rect x="15" y="2" width="5" height="5" fill="#1a84cf"/></svg>Network cabling</div>
<div class="abs feature" style="left:664px;top:1379px"><svg viewBox="0 0 22 22"><circle cx="11" cy="11" r="3" fill="#1a84cf"/><circle cx="4" cy="4" r="2.5" fill="#1a84cf"/><circle cx="18" cy="4" r="2.5" fill="#1a84cf"/><circle cx="4" cy="18" r="2.5" fill="#1a84cf"/><circle cx="18" cy="18" r="2.5" fill="#1a84cf"/><path d="M4 4 L18 18 M18 4 L4 18" stroke="#1a84cf" stroke-width="1.5"/></svg>Network Security</div>
<div class="abs feature" style="left:923px;top:1379px"><svg viewBox="0 0 22 22"><rect x="2" y="3" width="18" height="12" fill="none" stroke="#1a84cf" stroke-width="2"/><path d="M7 19 h8 M11 15 v4" stroke="#1a84cf" stroke-width="2"/></svg>Desktop Support</div>

<h2 class="abs sec-title out-title"><span class="sq sm"></span>OUTSOURCING TECHNOLOGY</h2>
<p class="abs out-text">In today's world, companies are expected to use technology to function and stay competitive. However, this aspect of business provides many challenges that most companies cannot solve on their own. Outsourcing technology provides solutions to almost every aspect of your business and can increase your profits.</p>
<div class="abs out-more"><span class="read-more">READ MORE<b>»</b></span></div>
<div class="abs img-block img-team" role="img" aria-label="Photo of two colleagues looking at a computer screen in an office"></div>

<!-- testimonial -->
<h2 class="abs sec-title testi-title"><span class="sq"></span>TESTIMONIAL</h2>
<div class="abs testi-sub">What People Say About Harlow &amp; Pine, P.C from Our Customer</div>
<div class="abs quote-box">"Lorem Ipsum is simply dummy text of the printing and typesetting industry. Lorem Ipsum has been the industry's standard dummy text ever since the 1500s, when an unknown printer took a galley of type and scrambled it to make a type specimen book."</div>
<div class="abs quote-mark">“</div>
<svg class="abs quote-tail" width="30" height="26" viewBox="0 0 30 26"><polygon points="0,0 30,0 28,26" fill="#1a84cf"/></svg>
<div class="abs client">-Client Name</div>
<div class="abs dots"><span></span><span class="on"></span><span></span><span></span><span></span><span></span></div>

<!-- footer -->
<div class="abs footer"></div>
<div class="abs f-col" style="left:79px">
  <h4>USEFULL LINKS</h4>
  <ul class="f-links"><li>Home</li><li>About</li><li>Services</li><li>Careers</li><li>Solution</li><li>Contact</li></ul>
</div>
<div class="abs f-col f-news" style="left:457px">
  <h4>NEWSLETTER</h4>
  <p>Lorem Ipsum is simply dummy text of the printing and typesetting.</p>
  <div class="f-input">Email Id<svg width="22" height="20" viewBox="0 0 22 20"><path d="M1 9 L21 1 L15 19 L10 11 Z M10 11 L21 1" fill="none" stroke="#0f2d55" stroke-width="1.5"/></svg></div>
  <div class="f-btn">SUBMIT</div>
</div>
<div class="abs f-col f-contact" style="left:816px">
  <h4>CONTACT US</h4>
  <div class="row"><svg width="18" height="18" viewBox="0 0 18 18"><path d="M9 1 v16 M2 5 h14 M3 10 h12" stroke="#e4eef8" stroke-width="2"/></svg><div>Kelvanbrook Technology Group, Inc.<br>1840 Marlowe Ave.<br>Fairhaven, Texas 77390</div></div>
  <div class="row"><svg width="18" height="18" viewBox="0 0 18 18"><path d="M4 1 l4 4 l-2 2 c1 2 3 4 5 5 l2 -2 l4 4 l-3 3 c-6 -1 -12 -7 -13 -13z" fill="#e4eef8"/></svg><div>(555) 310-4827</div></div>
  <div class="row"><svg width="18" height="14" viewBox="0 0 18 14"><rect x="1" y="1" width="16" height="12" fill="#e4eef8"/><path d="M1 1 l8 6 l8 -6" stroke="#17599b" stroke-width="1.5" fill="none"/></svg><div>info@kelvanbrook.com</div></div>
</div>
<div class="abs copy">© <b>Kelvanbrook Technology Group,Inc.</b> - 2017 All Right Reserved</div>

</body>
</html>
```